Business Card Design

I'm a commercial general contractor remodel offices, hotels, health clubs and stores mostly San Francisco and the peninsula
the file I down loaded is kind of what I want I like the I beam with my company name in it, that would be fine with me but if you have better Idea will look at it you never know, I'm decided to give in and change my company name to how every one knows me, I have been in business since 1991, I like the I beam logo I included one of my old card from my old company for reference for you.

BROCK CONSTRUCTION (is my company name)
Warren Pelkey contractor, LIc 514387
3148 Larkspur Row, San Bruno, California 94071
mobile, (415) 736-4052
phone (650) 514-2087
Fax, (650) 514-2088
email, brock@brockconstruction.example

```html
<!DOCTYPE html>
<html lang="en">
<head>
<meta charset="utf-8">
<title>Brock Construction – Business Card</title>
<link rel="stylesheet" href="https://fonts.googleapis.com/css2?family=Tinos:wght@400;700&display=swap">
<style>
  :root {
    --page-bg: #d9d9d9;
    --card-black: #1c1c1e;
    --card-black-edge: #2a2a2c;
    --band-white: #fbfbfb;
    --brand-blue: #2f86c6;
    --brand-blue-light: #6fb3e3;
    --text-light: #e9e9e9;
    --text-muted: #9a9a9a;
    --skyline-dark: #151515;
    --skyline-mid: #3a3a3a;
  }
  * { box-sizing: border-box; margin: 0; padding: 0; }
  html, body {
    width: 1200px; height: 900px; overflow: hidden;
    background: var(--page-bg);
    font-family: "Tinos", "Times New Roman", serif;
  }
  .canvas { position: relative; width: 1200px; height: 900px; }

  .business-card {
    position: absolute; left: 100px; top: 164px;
    width: 1000px; height: 572px;
    background: linear-gradient(180deg, var(--card-black-edge), var(--card-black));
    overflow: hidden;
    box-shadow: 0 10px 30px rgba(0,0,0,.25);
  }

  .brand-band {
    position: absolute; left: 0; top: 0; width: 100%; height: 232px;
    background: var(--band-white);
  }
  .brand-mark {
    position: absolute; left: 62px; top: 42px;
    display: flex; align-items: center; gap: 14px;
  }
  .brand-mark__square {
    width: 26px; height: 26px; background: var(--brand-blue);
  }
  .brand-mark__name {
    font-size: 64px; font-weight: 700; color: var(--brand-blue);
    letter-spacing: 2px; line-height: 1;
  }
  .company-name {
    position: absolute; left: 62px; top: 140px;
    font-size: 30px; color: var(--brand-blue); letter-spacing: 1px;
    white-space: nowrap;
  }

  .skyline {
    position: absolute; left: 490px; top: 56px;
    width: 450px; height: 262px;
    background: linear-gradient(180deg, var(--skyline-mid), var(--skyline-dark));
  }

  .divider {
    position: absolute; left: 0; top: 318px; width: 490px; height: 2px;
    background: linear-gradient(90deg, var(--brand-blue), var(--brand-blue-light) 70%, transparent);
  }

  .person {
    position: absolute; left: 62px; top: 250px;
  }
  .person__name {
    font-size: 32px; color: var(--brand-blue); letter-spacing: 1px; text-transform: uppercase;
  }
  .person__title {
    font-size: 19px; color: var(--text-muted); margin-top: 2px;
  }

  .contact-left {
    position: absolute; left: 62px; top: 346px;
    font-size: 21px; line-height: 1.3; color: var(--text-light);
    list-style: none;
  }
  .contact-right {
    position: absolute; right: 60px; top: 388px;
    font-size: 24px; line-height: 1.35; color: var(--text-light);
    text-align: right; list-style: none;
  }
  .contact-right .license { font-size: 28px; margin-bottom: 4px; }
</style>
</head>
<body>
<main class="canvas">
  <article class="business-card">
    <header class="brand-band">
      <div class="brand-mark">
        <span class="brand-mark__square"></span>
        <span class="brand-mark__name">BROCK</span>
      </div>
      <div class="company-name">BROCK CONSTRUCTION</div>
    </header>

    <div class="skyline" role="img" aria-label="City skyline silhouette of office towers"></div>

    <div class="person">
      <div class="person__name">Warren Pelkey</div>
      <div class="person__title">President</div>
    </div>
    <div class="divider"></div>

    <ul class="contact-left">
      <li>Email : brock@brockconstruction.example</li>
      <li>Add : 3148 Larkspur Row</li>
      <li>San Bruno, Ca 94071</li>
      <li>www.brockconstruction.example</li>
    </ul>

    <ul class="contact-right">
      <li class="license">Lic #514387</li>
      <li>Telephone : (650) 514-2087</li>
      <li>Fax : (650) 514-2088</li>
      <li>Cell : (415) 736-4052</li>
    </ul>
  </article>
</main>
</body>
</html>
```